Building company buisness cards

We are looking for a sharp modern new look for our business cards.We are a New Zealand based company that specialises in house and land packages.We have attached a photo of the current logo and would like to see if it can be improved somehow if needed.We are open to any colours but we have chosen Black and White at this stage. Feel free to change the font and make the logo smarter looking.Play with the colours and see what looks best.We want a card that looks so good know one will want to throw it away!

Target Market(s)

Building profesonals, home buyers

Industry/Entity Type

Building

Contact Information for Business Card

Garrick Tenwood
0275390628
garrickt@hartvale.co.nz

Font styles to use
Serif
Sans Serif

Colors

Designer to choose colors to be used in the design.

Requirements
Must have
• Just the logo on one side and details on the other
• Clean simple looking card
Nice to have
• Round corners and detail like raised or spot UV
• Something that stands out
Should not have
• To title needed, Director etc

```html
<!DOCTYPE html>
<html lang="en">
<head>
<meta charset="utf-8">
<title>Hartvale business cards</title>
<link rel="stylesheet" href="https://fonts.googleapis.com/css2?family=Open+Sans:wght@300;400&display=swap">
<style>
  :root {
    --backdrop: #262626;
    --card-black: #1a1a1a;
    --spot-gloss: #4a4a4a;
    --card-white: #ffffff;
    --ink: #151515;
    --ink-soft: #2a2a2a;
  }
  * { margin: 0; padding: 0; box-sizing: border-box; }
  html, body {
    width: 1200px;
    height: 942px;
    overflow: hidden;
    background: var(--backdrop);
  }
  .stage {
    width: 1200px;
    height: 942px;
    display: flex;
    align-items: center;
    justify-content: center;
    gap: 60px;
  }
  .card {
    position: relative;
    width: 520px;
    height: 318px;
    border-radius: 26px;
    overflow: hidden;
  }
  .card--logo-side { background: var(--card-black); }
  .card--details-side { background: var(--card-white); }

  .brand-name {
    font-family: "Open Sans", Arial, sans-serif;
    font-weight: 400;
    font-size: 52px;
    line-height: 1;
    letter-spacing: 1px;
  }

  .card--logo-side .brand-name {
    position: absolute;
    left: 50%;
    top: 50%;
    transform: translate(-50%, -50%);
    color: var(--spot-gloss);
  }

  .card--details-side .brand-name {
    position: absolute;
    left: 44px;
    top: 56px;
    color: var(--ink);
  }

  .contact {
    position: absolute;
    left: 250px;
    top: 196px;
    font-family: "Open Sans", Arial, sans-serif;
    color: var(--ink);
  }
  .contact__name {
    font-weight: 300;
    font-size: 22px;
    margin-bottom: 8px;
  }
  .contact__line {
    display: flex;
    align-items: center;
    gap: 8px;
    font-weight: 400;
    font-size: 14px;
    color: var(--ink-soft);
    line-height: 22px;
  }
  .contact__icon { width: 11px; height: 11px; flex: none; }
</style>
</head>
<body>
<main class="stage">
  <section class="card card--logo-side" aria-label="Card front with brand name">
    <span class="brand-name">Hartvale</span>
  </section>

  <section class="card card--details-side" aria-label="Card back with contact details">
    <span class="brand-name">Hartvale</span>
    <div class="contact">
      <p class="contact__name">Garrick Tenwood</p>
      <p class="contact__line">
        <svg class="contact__icon" viewBox="0 0 12 12" aria-hidden="true">
          <rect x="0" y="0" width="12" height="12" rx="1.5" fill="#151515"/>
          <path d="M3.2 2.6c.4-.3.9-.2 1.1.2l.6 1.2c.2.3.1.7-.2.9l-.4.3c.4.9 1.1 1.6 2 2l.3-.4c.2-.3.6-.4.9-.2l1.2.6c.4.2.5.7.2 1.1l-.5.6c-.4.4-1 .5-1.5.3C5 8.7 3.3 7 2.6 5.1c-.2-.5-.1-1.1.3-1.5z" fill="#fff"/>
        </svg>
        0275390628
      </p>
      <p class="contact__line">
        <svg class="contact__icon" viewBox="0 0 12 12" aria-hidden="true">
          <rect x="0" y="0" width="12" height="12" rx="1.5" fill="#151515"/>
          <rect x="2" y="3.5" width="8" height="5.5" fill="none" stroke="#fff" stroke-width="1"/>
          <path d="M2 3.5 6 6.6 10 3.5" fill="none" stroke="#fff" stroke-width="1"/>
        </svg>
        garrickt@hartvale.co.nz
      </p>
    </div>
  </section>
</main>
</body>
</html>
```